Quarry Desk Fellows needs a Ad design for products page

We need an Ad design on multiple formats for our website https://www.quarrydeskfellows.com. Our products are mainly reports and guide for PWLT and Velora. We want to make sure people will see our products page easier with this ad banner. We would like to use kindly the same colors from our blog site. The Ad banner must be attractive, neutral colors and modern ad.

Target Market(s)

IT and Brontavix Products

Font styles to use
Other font styles liked:
• Google Font Lato

Colors
0792cd

Requirements
Must have
• We would like to use kindly the same colors from our blog site. The Ad banner must be attractive, neutral colors and modern ad.
Nice to have
• Nothing for the moment
Should not have
• Animation, no flashy

```html
<!DOCTYPE html>
<html lang="en">
<head>
<meta charset="utf-8">
<title>Quarry Desk Fellows – Banner Ad Set</title>
<link href="https://fonts.googleapis.com/css2?family=Lato:wght@400;700;900&display=swap" rel="stylesheet">
<style>
  :root {
    --stage: #b5b5b5;
    --ink: #0d3447;
    --brand: #0792cd;
    --brand-deep: #0a6fb0;
    --sky: #d4f0fc;
    --mist: #c3d6de;
    --label: #1e5a78;
    --paper: #ffffff;
  }
  * { margin: 0; padding: 0; box-sizing: border-box; }
  html, body { width: 1200px; height: 1000px; overflow: hidden; }
  body { background: var(--stage); font-family: 'Lato', sans-serif; position: relative; }

  .banner { position: absolute; background: var(--paper); overflow: hidden; }
  .banner .swoosh { position: absolute; inset: 0; width: 100%; height: 100%; }
  .line { position: absolute; line-height: 1; white-space: nowrap; color: var(--ink); }
  .centered { left: 0; width: 100%; text-align: center; }
  .lead { font-weight: 400; }
  .headline { font-weight: 900; }
  .cta { font-weight: 400; color: var(--brand); }
  .url { font-weight: 700; }

  .brand-name { position: absolute; color: var(--brand); font-weight: 400; white-space: nowrap; line-height: 1; }
  .brand-dot { position: absolute; border-radius: 50%; background: var(--brand-deep); }

  .banner--wide-small { left: 33px; top: 53px; width: 478px; height: 287px; }
  .banner--square { left: 35px; top: 355px; width: 258px; height: 258px; }
  .banner--tower { left: 531px; top: 53px; width: 275px; height: 559px; }
  .banner--skyscraper { left: 823px; top: 53px; width: 352px; height: 880px; }
  .banner--leaderboard { left: 33px; top: 627px; width: 770px; height: 306px; }

  .set-label {
    position: absolute; left: 300px; top: 432px; width: 226px;
    text-align: center; color: var(--label); font-weight: 700;
    font-size: 38px; letter-spacing: 4px; line-height: 50px;
  }
</style>
</head>
<body>

<!-- Horizontal small banner -->
<section class="banner banner--wide-small">
  <svg class="swoosh" viewBox="0 0 478 287" preserveAspectRatio="none" aria-hidden="true">
    <defs>
      <linearGradient id="g1" x1="0" y1="0" x2="1" y2="1">
        <stop offset="0" stop-color="#c3d6de"/><stop offset="1" stop-color="#1ea6de"/>
      </linearGradient>
    </defs>
    <rect width="478" height="287" fill="#d4f0fc"/>
    <path d="M0,95 C210,92 390,165 448,287 H0 Z" fill="#ffffff"/>
    <path d="M0,0 H210 C340,20 440,120 478,235 V287 H468 C420,150 270,48 0,42 Z" fill="#0792cd"/>
    <path d="M0,70 C230,66 405,168 462,287 H446 C385,182 225,88 0,84 Z" fill="url(#g1)"/>
  </svg>
  <span class="brand-name" style="right:6px; top:7px; font-size:20px;">Quarry Desk Fellows</span>
  <span class="brand-dot" style="left:360px; top:36px; width:100px; height:100px;"></span>
  <span class="line lead" style="left:11px; top:92px; font-size:26px;">TO KNOW</span>
  <span class="line lead" style="left:11px; top:124px; font-size:26px;">MORE ABOUT</span>
  <span class="line headline" style="left:11px; top:157px; font-size:38px;">PWLT &amp; VELORA</span>
  <span class="line cta" style="left:11px; top:199px; font-size:33px;">VISIT OUR WEBSITE:</span>
  <span class="line url" style="left:11px; top:242px; font-size:21px;">www.quarrydeskfellows.com</span>
</section>

<!-- Square banner -->
<section class="banner banner--square">
  <svg class="swoosh" viewBox="0 0 258 258" preserveAspectRatio="none" aria-hidden="true">
    <defs>
      <linearGradient id="g2" x1="0" y1="0" x2="1" y2="1">
        <stop offset="0" stop-color="#c3d6de"/><stop offset="1" stop-color="#1ea6de"/>
      </linearGradient>
    </defs>
    <rect width="258" height="258" fill="#d4f0fc"/>
    <path d="M0,58 C140,70 215,160 236,258 H0 Z" fill="#ffffff"/>
    <path d="M0,0 H80 C170,30 235,100 258,180 V258 H252 C228,160 150,55 0,30 Z" fill="#0792cd"/>
    <path d="M0,42 C150,60 230,160 248,258 H238 C218,165 140,68 0,56 Z" fill="url(#g2)"/>
  </svg>
  <span class="brand-name" style="right:4px; top:3px; font-size:13px;">Quarry Desk Fellows</span>
  <span class="brand-dot" style="left:172px; top:26px; width:72px; height:72px;"></span>
  <span class="line lead" style="left:11px; top:71px; font-size:23px;">FOR</span>
  <span class="line lead" style="left:11px; top:96px; font-size:23px;">MORE</span>
  <span class="line lead" style="left:11px; top:120px; font-size:23px;">DETAILS</span>
  <span class="line cta" style="left:11px; top:151px; font-size:30px;">VISIT OUR</span>
  <span class="line cta" style="left:11px; top:187px; font-size:30px;">WEBSITE:</span>
  <span class="line url" style="left:11px; top:231px; font-size:13px;">www.quarrydeskfellows.com</span>
</section>

<div class="set-label">SAMPLE<br>BANNER<br>ADS</div>

<!-- Vertical medium banner -->
<section class="banner banner--tower">
  <svg class="swoosh" viewBox="0 0 275 559" preserveAspectRatio="none" aria-hidden="true">
    <defs>
      <linearGradient id="g3" x1="0" y1="0" x2="1" y2="1">
        <stop offset="0" stop-color="#c3d6de"/><stop offset="1" stop-color="#1ea6de"/>
      </linearGradient>
    </defs>
    <path d="M0,0 H275 V170 C220,110 120,80 0,78 Z" fill="#d4f0fc"/>
    <path d="M0,5 C120,10 230,70 275,140 V170 C220,100 120,40 0,32 Z" fill="#0792cd"/>
    <path d="M0,62 C130,62 230,110 275,180 V195 C225,130 120,78 0,74 Z" fill="url(#g3)"/>
  </svg>
  <span class="line lead centered" style="top:134px; font-size:27px;">TO KNOW</span>
  <span class="line lead centered" style="top:166px; font-size:27px;">MORE ABOUT</span>
  <span class="line headline centered" style="top:193px; font-size:48px;">PWLT &amp;</span>
  <span class="line headline centered" style="top:244px; font-size:48px;">VELORA</span>
  <span class="line cta centered" style="top:292px; font-size:45px;">VISIT OUR</span>
  <span class="line cta centered" style="top:336px; font-size:45px;">WEBSITE:</span>
  <span class="line url centered" style="top:388px; font-size:15px;">www.quarrydeskfellows.com</span>
  <span class="brand-dot" style="left:95px; top:428px; width:86px; height:86px;"></span>
  <span class="brand-name centered" style="top:530px; font-size:20px;">Quarry Desk Fellows</span>
</section>

<!-- Skyscraper banner -->
<section class="banner banner--skyscraper">
  <svg class="swoosh" viewBox="0 0 352 880" preserveAspectRatio="none" aria-hidden="true">
    <defs>
      <linearGradient id="g4" x1="0" y1="0" x2="1" y2="1">
        <stop offset="0" stop-color="#c3d6de"/><stop offset="1" stop-color="#1ea6de"/>
      </linearGradient>
    </defs>
    <path d="M0,0 H352 V200 C280,130 150,100 0,98 Z" fill="#d4f0fc"/>
    <path d="M0,20 C150,22 290,90 352,165 V200 C280,120 150,60 0,52 Z" fill="#0792cd"/>
    <path d="M0,82 C160,84 290,140 352,215 V230 C280,160 150,104 0,98 Z" fill="url(#g4)"/>
  </svg>
  <span class="line lead centered" style="top:209px; font-size:38px;">TO KNOW</span>
  <span class="line lead centered" style="top:259px; font-size:38px;">MORE ABOUT</span>
  <span class="line headline centered" style="top:309px; font-size:64px;">PWLT &amp;</span>
  <span class="line headline centered" style="top:378px; font-size:64px;">VELORA</span>
  <span class="line cta centered" style="top:451px; font-size:62px;">VISIT OUR</span>
  <span class="line cta centered" style="top:519px; font-size:62px;">WEBSITE:</span>
  <span class="line url centered" style="top:613px; font-size:20px;">www.quarrydeskfellows.com</span>
  <span class="brand-dot" style="left:116px; top:680px; width:120px; height:120px;"></span>
  <span class="brand-name centered" style="top:836px; font-size:27px;">Quarry Desk Fellows</span>
</section>

<!-- Leaderboard banner -->
<section class="banner banner--leaderboard">
  <svg class="swoosh" viewBox="0 0 770 306" preserveAspectRatio="none" aria-hidden="true">
    <defs>
      <linearGradient id="g5" x1="0" y1="0" x2="1" y2="1">
        <stop offset="0" stop-color="#c3d6de"/><stop offset="1" stop-color="#1ea6de"/>
      </linearGradient>
    </defs>
    <rect width="770" height="306" fill="#d4f0fc"/>
    <path d="M0,142 C90,108 220,56 380,56 C580,58 692,180 722,306 H0 Z" fill="#ffffff"/>
    <path d="M0,118 C90,80 220,28 380,28 C600,30 720,160 750,306 H722 C692,180 580,58 380,56 C220,56 90,108 0,142 Z" fill="url(#g5)"/>
    <path d="M0,85 C200,-10 600,-60 770,160 V306 H750 C720,160 600,30 380,28 C220,26 90,80 0,118 Z" fill="#0792cd"/>
  </svg>
  <span class="brand-name" style="right:6px; top:6px; font-size:21px;">Quarry Desk Fellows</span>
  <span class="brand-dot" style="left:652px; top:38px; width:100px; height:100px;"></span>
  <span class="line lead centered" style="top:89px; font-size:27px;">TO KNOW MORE ABOUT</span>
  <span class="line headline centered" style="top:129px; font-size:52px;">PWLT &amp; VELORA</span>
  <span class="line cta centered" style="top:192px; font-size:47px;">VISIT OUR WEBSITE:</span>
  <span class="line url centered" style="top:248px; font-size:42px;">www.quarrydeskfellows.com</span>
</section>

</body>
</html>
```